I need a website designed for my hair extensions business

I have some before and afters you can use

https://example-photos.net/p/Qm4trLwKoBa/

https://www.example-photos.net/p/Hvno7PaWkeR/?sid=QtPwZjN0cVhkYmRxUb==
Hi I offer tiny weave hair extensions
My instagram page is Virelahairextensionsstudio

I’m needing a Lux website
I have been doing weave hair extensions for 16 years and I specialise in only the finest installation and hair quality

The website must attract a high profile cliental

I have thousands of photos on my instagram page you can use

The website must be coded to attract hair extensions clients from all over Victoria Australia
It must have what’s relevant for google to recognise the website to Potential clients

recognise

Some are the below
Apologies for the confusion. Here are some SEO keywords that can be used for a website focused on Weave Hair Extensions in Victoria, Australia:

1. Weave hair extensions Victoria
2. Best weave hair extensions Australia
3. Affordable weave hair extensions
4. Professional weave hair extensions
5. High-quality weave hair extensions
6. Victoria weave hair extension services
7. Top-rated weave hair extension salon
8. Natural-looking weave hair extensions
9. Customizable weave hair extensions
10. Victoria's premier weave hair extensions

Remember to incorporate these keywords strategically into your website's content, including titles, headings, meta descriptions, and throughout the body text. This will help improve your website's visibility in search engine results and attract relevant traffic from individuals looking for weave hair extensions in Victoria, Australia.

Please make the website look elegant not tacky no pink or script writing please

Target Market(s)

Woman between 21 to 60

Industry/Entity Type

https://www.example-photos.net/reel/KpwwoTYBv7M/?sid=QtPwZjN0cVhkYmRxUb==

Coding

Coded - Design and coding required

Number of Pages Required

3 page

Requirements
Must have
• Description of myself 16 years experience, I’ve installed 1000s of weave hair extensions, my intention to deal is guaranteed.
Nice to have
• I have added 2 images or how flat and tiny the weave hair extensions are, here is a link to a video that can be used https://www.example-photos.net/reel/KpwwoTYBv7M/?sid=QtPwZjN0cVhkYmRxUb== The website should look elegant, the extensions I install are spectacular. You can see the before and after on my instagram page virela hair extensions studio. The pictures of my work should be taken from my instagram page as I own those photos
Should not have
• My website should not have pink or script writing it needs to attract a high cliental the website must look elegant

```html
<!DOCTYPE html>
<html lang="en">
<head>
<meta charset="utf-8">
<title>Virela Hair Extensions – Homepage Options</title>
<link href="https://fonts.googleapis.com/css2?family=Jost:wght@200;300;400;500;600;700&family=Playfair+Display:wght@400;500&display=swap" rel="stylesheet">
<style>
:root{
  --accent:#d9865a;
  --accent-dark:#b96a43;
  --mocha:#5b4034;
  --ink-dark:#0f0f0f;
  --panel-dark:#161616;
  --panel-deep:#101010;
  --board-light:#ffffff;
  --board-dark:#333333;
  --text-light:#f2f2f2;
  --text-muted:#9a9a9a;
  --serif:'Playfair Display',Georgia,serif;
  --sans:'Jost',Arial,sans-serif;
}
*{margin:0;padding:0;box-sizing:border-box}
html,body{width:1200px;height:2583px;overflow:hidden}
body{position:relative;font-family:var(--sans);background:var(--board-dark)}
.board{position:absolute;top:0;height:2583px}
.board--light{left:0;width:580px;background:var(--board-light)}
.board--dark{left:580px;width:620px;background:var(--board-dark)}
.option-label{position:absolute;top:82px;width:100%;text-align:center;font:700 26px/1 var(--sans);letter-spacing:3px}
.board--light .option-label{color:#111}
.board--dark .option-label{color:#fff}

.site{position:absolute;top:135px;width:457px;height:2395px;overflow:hidden;color:var(--text-light)}
.board--light .site{left:61px}
.board--dark .site{left:79px}
.site--noir{--surface:#161616;--surface-alt:#1b1b1b;--ink:#f2f2f2;--ink-soft:#9a9a9a;--topbar:transparent;--header:transparent;--cell:#141414}
.site--ivory{--surface:#ffffff;--surface-alt:#ffffff;--ink:#1a1a1a;--ink-soft:#777;--topbar:var(--accent);--header:#ffffff;--cell:#ffffff}

.abs{position:absolute}
.photo{position:absolute}
.eyebrow{position:absolute;font:400 5px/1 var(--sans);letter-spacing:.6px;color:var(--accent);text-transform:uppercase}
.heading{position:absolute;font:400 17px/1.1 var(--serif)}
.copy{position:absolute;font:400 4.6px/1.9 var(--sans);color:var(--text-muted)}
.btn{position:absolute;height:16px;background:var(--accent);color:#fff;font:500 4.6px/16px var(--sans);letter-spacing:.4px;padding-left:6px;text-transform:uppercase;border:1px solid var(--accent)}
.btn::after{content:"›";position:absolute;right:0;top:0;width:14px;height:14px;background:var(--accent-dark);text-align:center;font-size:7px;line-height:13px}
.centered{left:0;width:100%;text-align:center}

/* top bar + header */
.topbar{position:absolute;top:0;left:0;width:457px;height:13px;background:var(--topbar);z-index:3}
.topbar .dot{position:absolute;top:4px;width:5px;height:5px;border-radius:50%;border:.8px solid #fff}
.topbar .info{position:absolute;top:3px;font:400 4.6px/7px var(--sans);color:#fff;display:flex;align-items:center;gap:3px}
.topbar svg{width:7px;height:7px}
.header{position:absolute;top:13px;left:0;width:457px;height:33px;background:var(--header);z-index:3}
.brand{position:absolute;left:25px;top:9px;font:300 15px/1 var(--sans);letter-spacing:2px;text-transform:uppercase}
.site--noir .brand{color:#ddd}
.site--ivory .brand{color:#555}
.menu{position:absolute;right:25px;top:14px;display:flex;gap:10px;font:400 4.6px/1 var(--sans);text-transform:uppercase}
.site--noir .menu{color:#ddd}
.site--ivory .menu{color:#333}
.menu .is-active{color:var(--accent)}

/* hero */
.hero{position:absolute;left:0;top:0;width:457px;height:288px;background:#111}
.hero-title{position:absolute;left:25px;top:125px;font:400 16px/1 var(--serif);color:#fff}
.hero-sub{position:absolute;left:25px;top:148px;font:200 22px/1 var(--sans);color:#fff;letter-spacing:.5px}
.hero-text{position:absolute;left:25px;top:182px;font:400 4.6px/1 var(--sans);color:#eee}
.hero-text b{color:var(--accent);font-weight:600}
.slider-dots{position:absolute;top:276px;display:flex;gap:3px}
.slider-dots i{width:2px;height:2px;border-radius:50%;background:#fff;opacity:.6}

/* about */
.about{position:absolute;top:288px;left:0;width:457px;height:235px}
.about-media{position:absolute;left:0;top:0;width:228px;height:235px;background:linear-gradient(135deg,#2a2420,#121110)}
.about-body{position:absolute;left:228px;top:0;width:229px;height:235px;background:var(--surface-alt)}
.about-body .heading{color:var(--ink)}
.badge{position:absolute;left:25px;top:160px;width:56px;height:18px;background:rgba(40,40,40,.9);display:flex;align-items:center;gap:3px;padding-left:5px}
.badge strong{font:500 11px/1 var(--sans);color:var(--accent)}
.badge span{font:400 3.8px/1.2 var(--sans);color:#fff}

/* offer */
.offer{position:absolute;top:523px;left:0;width:457px;height:305px;background:var(--surface)}
.offer .heading{color:var(--ink)}
.offer-caption{position:absolute;top:241px;font:400 7px/1 var(--serif);color:var(--ink)}
.offer-feature{position:absolute;left:143px;top:75px;width:170px;height:176px;background:linear-gradient(180deg,#6b6258,#c9b89c 55%,#3d3530)}
.offer-feature .cap{position:absolute;bottom:22px;width:100%;text-align:center;font:500 7.5px/1 var(--serif);color:#fff}
.offer-feature .sub{position:absolute;bottom:13px;width:100%;text-align:center;font:400 4px/1 var(--sans);color:#eee}
.pager{position:absolute;top:265px;font:400 4px/1 var(--sans);color:var(--ink-soft);text-transform:uppercase}

/* services */
.services{position:absolute;top:828px;left:0;width:457px;height:452px;background:#0f0f0f}
.service{position:absolute;width:131px}
.service .pic{width:131px;height:91px}
.service .tag{margin-top:11px;font:400 4.2px/1 var(--sans);color:var(--accent);text-transform:uppercase}
.service .name{margin-top:3px;font:400 7px/1.1 var(--serif);color:#eee}
.service .desc{margin-top:5px;font:400 4.2px/1.8 var(--sans);color:var(--text-muted)}
.service .desc em{font-style:normal;color:var(--accent)}

/* specialists */
.specialists{position:absolute;top:1280px;left:0;width:457px;height:272px;background:var(--surface)}
.specialists .heading{color:var(--ink)}
.before-after{position:absolute;font:400 5px/1 var(--sans);color:#fff;text-align:center;width:100%}

/* testimonials */
.testimonials{position:absolute;top:1552px;left:0;width:457px;height:223px;background:#121212}
.quote-card{position:absolute;top:70px;width:130px;height:76px;background:#1b1b1b;padding:8px 6px}
.quote-card .mark{font:700 10px/1 var(--serif);color:var(--accent)}
.quote-card p{margin-top:2px;font:400 4.2px/1.9 var(--sans);color:var(--text-muted)}
.reviewer{position:absolute;top:155px;display:flex;align-items:center;gap:5px}
.reviewer .avatar{width:17px;height:17px;border-radius:50%;background:linear-gradient(135deg,#caa58a,#6a4a3a)}
.reviewer b{display:block;font:600 5px/1 var(--sans);color:var(--accent);text-transform:uppercase}
.reviewer span{display:block;margin-top:2px;font:400 3.8px/1 var(--sans);color:var(--text-muted)}
.site--ivory .reviewer b{color:#fff}
.arrow-nav{position:absolute;top:105px;font:400 7px/1 var(--sans);color:#ccc}

/* keyword grid */
.keywords{position:absolute;top:1775px;left:0;width:457px;height:291px}
.cell{position:absolute;width:152px;height:97px}
.cell--text{background:var(--cell);padding:30px 0 0 22px}
.cell--mocha{background:var(--mocha)}
.cell small{display:block;font:500 4.6px/1 var(--sans);color:var(--ink)}
.cell strong{display:block;margin-top:6px;font:500 12px/1 var(--serif);color:var(--ink);text-transform:uppercase}
.cell span{display:block;margin-top:4px;font:300 8px/1 var(--sans);color:var(--accent);text-transform:uppercase;letter-spacing:.3px}
.cell--mocha small,.cell--mocha strong{color:#fff}
.cell--mocha span{color:#e2b59a}

/* newsletter */
.newsletter{position:absolute;top:2066px;left:0;width:457px;height:171px;background:radial-gradient(ellipse at 30% 40%,#2c2a28,#0e0e0e 70%)}
.newsletter .heading{color:#fff}
.signup{position:absolute;left:93px;top:97px;width:272px;height:18px;background:#fff;display:flex;align-items:center;padding-left:7px;gap:4px;font:400 4.4px/1 var(--sans);color:#999}
.signup svg{width:6px;height:6px}
.signup .btn{top:1px;right:1px;width:62px;height:16px}

/* footer */
.footer{position:absolute;top:2237px;left:0;width:457px;height:158px;background:var(--surface)}
.footer .brand{top:28px}
.footer-head{position:absolute;top:30px;font:500 5px/1 var(--sans);color:var(--accent);text-transform:uppercase}
.footer-links{position:absolute;top:44px;font:400 4.4px/12.2px var(--sans);color:var(--ink-soft)}
.contact-row{position:absolute;display:flex;gap:6px;font:400 4.2px/1.5 var(--sans);color:var(--ink-soft);align-items:flex-start}
.contact-row i{width:9px;height:9px;background:#3a3a3a;display:flex;align-items:center;justify-content:center;flex:none}
.site--ivory .contact-row i{background:#eee}
.contact-row svg{width:5px;height:5px}
.social-square{position:absolute;top:95px;width:10px;height:10px;background:var(--accent)}
.insta{position:absolute;left:320px;top:44px;display:grid;grid-template-columns:repeat(3,35px);gap:2px}
.insta div{height:25px}
.footer-bar{position:absolute;top:134px;left:0;width:457px;height:24px;border-top:1px solid rgba(128,128,128,.2);text-align:center;font:400 4.4px/24px var(--sans);color:var(--ink)}
.footer-bar b{font-weight:400;color:var(--accent)}
.footer-copy{position:absolute;left:25px;top:60px;width:100px;font:400 4.4px/1.8 var(--sans);color:var(--ink-soft)}
</style>
</head>
<body>

<!-- ============ OPTION 1 : NOIR ============ -->
<section class="board board--light">
  <h2 class="option-label">OPTION 1</h2>
  <div class="site site--noir">
    <div class="topbar">
      <span class="dot" style="left:25px"></span><span class="dot" style="left:35px"></span><span class="dot" style="left:45px"></span>
      <span class="info" style="left:276px"><svg viewBox="0 0 10 10"><circle cx="5" cy="5" r="4.5" fill="none" stroke="#fff" stroke-width=".8"/><path d="M3.3 3c.3 1.8 1.6 3.3 3.4 3.8l.5-.8-1-.6-.5.4c-.6-.3-1.1-.8-1.4-1.4l.4-.5-.6-1z" fill="#fff"/></svg>+61 3 9555 0180</span>
      <span class="info" style="left:345px"><svg viewBox="0 0 10 10"><circle cx="5" cy="5" r="4.5" fill="none" stroke="#fff" stroke-width=".8"/><rect x="2.8" y="3.5" width="4.4" height="3" fill="none" stroke="#fff" stroke-width=".6"/><path d="M2.8 3.5L5 5.2l2.2-1.7" fill="none" stroke="#fff" stroke-width=".6"/></svg>info@virelahairstudio.com</span>
    </div>

    <div class="hero">
      <div class="photo" role="img" aria-label="Woman with long glossy black hair smiling, hand in her hair" style="left:190px;top:0;width:267px;height:288px;background:radial-gradient(ellipse at 60% 45%,#6d6d6d,#222 55%,#111 80%)"></div>
      <p class="eyebrow" style="left:25px;top:115px">Specialise in</p>
      <h1 class="hero-title">Finest Installation</h1>
      <p class="hero-sub">&amp; HAIR QUALITY</p>
      <p class="hero-text">I have been doing weave hair extensions for <b>16 years</b></p>
      <a class="btn" style="left:25px;top:202px;width:70px">Explore more</a>
      <div class="slider-dots" style="left:226px"><i></i><i></i><i></i></div>
    </div>

    <header class="header">
      <div class="brand">Virela</div>
      <nav class="menu"><span class="is-active">Home</span><span>About us</span><span>Services</span><span>Gallery</span><span>News</span><span>Contact us</span></nav>
    </header>

    <section class="about">
      <div class="about-media">
        <div class="photo" role="img" aria-label="Portrait of a woman with long straight auburn hair extensions" style="left:40px;top:28px;width:147px;height:178px;background:linear-gradient(160deg,#e8e2dc,#b07548 45%,#7a4a2a)"></div>
        <div class="badge"><strong>16</strong><span>Years of<br>Experience</span></div>
      </div>
      <div class="about-body">
        <p class="eyebrow" style="left:36px;top:48px">Welcome to</p>
        <h2 class="heading" style="left:36px;top:58px">Virela Hair Extensions</h2>
        <p class="copy" style="left:36px;top:86px;width:170px">Sed ut perspiciatis unde omnis iste natus error sit voluptatem accusantium doloremque laudantium, totam rem aperiam, eaque ipsa quae ab illo inventore veritatis et quasi architecto beatae vitae dicta sunt explicabo. Nemo enim ipsam voluptatem quia voluptas sit aspernatur aut odit aut fugit, sed quia consequuntur magni dolores eos qui ratione voluptatem sequi nesciunt.</p>
        <a class="btn" style="left:36px;top:170px;width:62px">Read more</a>
      </div>
    </section>

    <section class="offer">
      <p class="eyebrow centered" style="top:35px">Victoria Australia</p>
      <h2 class="heading centered" style="top:45px">Hair Extensions Offer</h2>
      <div class="photo" role="img" aria-label="Back view of long straight platinum blonde flat hair extensions" style="left:25px;top:95px;width:110px;height:136px;background:linear-gradient(180deg,#5d6670,#d8d0c0 40%,#bdb3a0)"></div>
      <div class="offer-feature" role="img" aria-label="Back view of long blonde tiny hair extensions in a salon"><p class="cap">TinyHair Extension</p><p class="sub">Sed ut perspiciatis unde omnis iste natus error sit voluptatem</p></div>
      <div class="photo" role="img" aria-label="Back view of long blonde weave hair extensions" style="left:321px;top:95px;width:111px;height:136px;background:linear-gradient(180deg,#4a5560,#c7b99f 45%,#2a2a2a)"></div>
      <p class="offer-caption" style="left:25px">Flat Hair Extension</p>
      <p class="offer-caption" style="left:321px">Weave Hair Extension</p>
      <p class="pager" style="left:25px">⟵&nbsp;&nbsp;Prev</p>
      <p class="pager" style="right:25px">Next&nbsp;&nbsp;⟶</p>
    </section>

    <section class="services">
      <p class="eyebrow centered" style="top:35px">What we do</p>
      <h2 class="heading centered" style="top:45px;color:#fff">Our Services</h2>
      <div class="service" style="left:25px;top:75px"><div class="pic" role="img" aria-label="Stylist sectioning hair with clips" style="background:linear-gradient(135deg,#e0e0e0,#555)"></div><p class="tag">Victoria</p><p class="name">Weave hair Extensions</p><p class="desc">Duis aute irure dolor in reprehenderit in voluptate velit esse cillum... <em>Read More</em></p></div>
      <div class="service" style="left:163px;top:75px"><div class="pic" role="img" aria-label="Stylist straightening long blonde hair" style="background:linear-gradient(135deg,#8a6a40,#d8b070 50%,#e0c040)"></div><p class="tag">Australia</p><p class="name">Weave hair Extensions</p><p class="desc">Duis aute irure dolor in reprehenderit in voluptate velit esse cillum... <em>Read More</em></p></div>
      <div class="service" style="left:300px;top:75px"><div class="pic" role="img" aria-label="Stylist curling long brown hair" style="background:linear-gradient(135deg,#eee,#7a5a40 60%,#3a2a20)"></div><p class="tag">Professional</p><p class="name">Weave hair Extensions</p><p class="desc">Duis aute irure dolor in reprehenderit in voluptate velit esse cillum... <em>Read More</em></p></div>
      <div class="service" style="left:25px;top:228px"><div class="pic" role="img" aria-label="Hands attaching a blonde extension weft" style="background:linear-gradient(135deg,#f0e0c0,#d8a860)"></div><p class="tag">High-quality</p><p class="name">Weave hair Extensions</p><p class="desc">Duis aute irure dolor in reprehenderit in voluptate velit esse cillum... <em>Read More</em></p></div>
      <div class="service" style="left:163px;top:228px"><div class="pic" role="img" aria-label="Stylist parting dark hair to fit extensions" style="background:linear-gradient(135deg,#8a6a55,#4a3020)"></div><p class="tag">Natural-looking</p><p class="name">Weave hair Extensions</p><p class="desc">Duis aute irure dolor in reprehenderit in voluptate velit esse cillum... <em>Read More</em></p></div>
      <div class="service" style="left:300px;top:228px"><div class="pic" role="img" aria-label="Hair extension bundles with scissors and tools" style="background:linear-gradient(135deg,#2a2a2a,#9a7040 55%,#1a1a1a)"></div><p class="tag">Customizable</p><p class="name">Weave hair Extensions</p><p class="desc">Duis aute irure dolor in reprehenderit in voluptate velit esse cillum... <em>Read More</em></p></div>
      <a class="btn" style="left:188px;top:400px;width:80px">View all services</a>
    </section>

    <section class="specialists">
      <div class="photo" role="img" aria-label="Two women in camel blazers with long brunette hair" style="left:0;top:36px;width:160px;height:202px;background:linear-gradient(160deg,#f0ece8,#c49a78 55%,#4a3528)"></div>
      <p class="eyebrow" style="left:183px;top:35px">Certified</p>
      <h2 class="heading" style="left:183px;top:45px">Hair Extension Specialists</h2>
      <p class="copy" style="left:183px;top:72px;width:248px">Sed ut perspiciatis unde omnis iste natus error sit voluptatem accusantium doloremque laudantium, totam rem aperiam eaque ipsa quae ab illo inventore veritatis et quasi architecto beatae vitae dicta sunt...</p>
      <a class="btn" style="left:183px;top:115px;width:62px">Read more</a>
      <div class="photo" role="img" aria-label="Before: woman with short thin blonde hair" style="left:288px;top:142px;width:81px;height:97px;background:linear-gradient(180deg,#e8e4e0,#c8b090 50%,#9a5a50)"><p class="before-after" style="bottom:8px">Before</p></div>
      <div class="photo" role="img" aria-label="After: woman with long voluminous blonde hair" style="left:377px;top:170px;width:80px;height:100px;background:linear-gradient(160deg,#e8c070,#d09040 55%,#b03020)"><p class="before-after" style="bottom:8px">After</p></div>
    </section>

    <section class="testimonials">
      <p class="eyebrow centered" style="top:35px">Testimonials</p>
      <h2 class="heading centered" style="top:45px;color:#fff">Our Satisfied Customer</h2>
      <span class="arrow-nav" style="left:11px">‹</span><span class="arrow-nav" style="right:11px">›</span>
      <div class="quote-card" style="left:25px"><p class="mark">“</p><p>“Sed ut perspiciatis unde omnis iste natus error sit voluptatem accusantium doloremque laudantium, totam rem aperiam, eaque ipsa quae ab illo inventore veritatis et quasi architecto beatae enim ipsam voluptatem quia voluptas sit”</p></div>
      <div class="quote-card" style="left:163px"><p class="mark">“</p><p>“Sed ut perspiciatis unde omnis iste natus error sit voluptatem accusantium doloremque laudantium, totam rem aperiam, eaque ipsa quae ab illo inventore veritatis et quasi architecto beatae enim ipsam voluptatem quia voluptas sit”</p></div>
      <div class="quote-card" style="left:300px"><p class="mark">“</p><p>“Sed ut perspiciatis unde omnis iste natus error sit voluptatem accusantium doloremque laudantium, totam rem aperiam, eaque ipsa quae ab illo inventore veritatis et quasi architecto beatae enim ipsam voluptatem quia voluptas sit”</p></div>
      <div class="reviewer" style="left:25px"><div class="avatar" role="img" aria-label="Customer portrait"></div><div><b>Mara Ellison</b><span>Happy Customer</span></div></div>
      <div class="reviewer" style="left:163px"><div class="avatar" role="img" aria-label="Customer portrait"></div><div><b>Tessa Dunmore</b><span>Happy Customer</span></div></div>
      <div class="reviewer" style="left:300px"><div class="avatar" role="img" aria-label="Customer portrait"></div><div><b>Clara Whitby</b><span>Happy Customer</span></div></div>
    </section>

    <section class="keywords">
      <div class="cell photo" role="img" aria-label="Blonde woman with long wavy hair" style="left:0;top:0;background:linear-gradient(135deg,#e8d8c0,#b09070)"></div>
      <div class="cell cell--text" style="left:152px;top:0"><small>Affordable</small><strong>Weave</strong><span>Hair Extensions</span></div>
      <div class="cell photo" role="img" aria-label="Black and white portrait of a woman with long dark hair in a satin dress" style="left:304px;top:0;width:153px;height:194px;background:linear-gradient(160deg,#bbb,#555 60%,#222)"></div>
      <div class="cell cell--text" style="left:0;top:97px"><small>Victoria</small><strong>Weave Hair</strong><span>Extensions Service</span></div>
      <div class="cell photo" role="img" aria-label="Stylist blow-drying a client's long brown hair" style="left:152px;top:97px;background:linear-gradient(135deg,#3a5a70,#8a6a50)"></div>
      <div class="cell photo" role="img" aria-label="Woman with long black hair beside pink blossoms" style="left:0;top:194px;background:linear-gradient(135deg,#e8c8c8,#2a2a2a 60%,#d8b0b0)"></div>
      <div class="cell cell--text" style="left:152px;top:194px"><small>Top-Rated</small><strong>Weave Hair</strong><span>Extensions Salon</span></div>
      <div class="cell cell--text cell--mocha" style="left:304px;top:194px;width:153px"><small>Victoria's</small><strong>Premier</strong><span>Wave Hair Extensions</span></div>
    </section>

    <section class="newsletter" role="img" aria-label="Dark background portrait of a woman with flowing hair">
      <p class="eyebrow centered" style="top:47px">Subscribe</p>
      <h2 class="heading centered" style="top:57px">Our Newsletter</h2>
      <p class="copy centered" style="top:78px;color:#bbb">Duis aute irure dolor in reprehenderit in voluptate velit esse cillum dolore</p>
      <div class="signup"><svg viewBox="0 0 10 10"><rect x="1" y="2" width="8" height="6" fill="none" stroke="#999"/><path d="M1 2l4 3 4-3" fill="none" stroke="#999"/></svg>Enter Your Email<a class="btn">Subscribe</a></div>
    </section>

    <footer class="footer">
      <div class="brand">Virela</div>
      <p class="footer-copy">Duis aute irure dolor in reprehenderit in voluptate velit esse cillum dolore eu fugiat nulla pariatur...</p>
      <span class="social-square" style="left:25px"></span><span class="social-square" style="left:40px"></span><span class="social-square" style="left:55px"></span>
      <p class="footer-head" style="left:140px">Quick links</p>
      <p class="footer-links" style="left:140px">Home<br>About Us<br>Services<br>Gallery<br>News<br>Contact Us</p>
      <p class="footer-head" style="left:215px">Contacts</p>
      <div class="contact-row" style="left:215px;top:44px;width:90px"><i><svg viewBox="0 0 10 10"><path d="M5 1a3 3 0 0 1 3 3c0 2.3-3 5-3 5S2 6.3 2 4a3 3 0 0 1 3-3z" fill="var(--accent)"/></svg></i>12 Lorem ipsum dolor sit amet<br>Geelong VIC 3220</div>
      <div class="contact-row" style="left:215px;top:69px"><i><svg viewBox="0 0 10 10"><path d="M2 1.5c.4 3.4 3 6 6.5 6.6l.8-1.6-2-1.2-1 .8C5 5.5 4.3 4.8 3.9 3.8l.8-1-1.2-2z" fill="var(--accent)"/></svg></i>+61 3 9555 0180</div>
      <div class="contact-row" style="left:215px;top:91px"><i><svg viewBox="0 0 10 10"><rect x="1.5" y="2.5" width="7" height="5" fill="none" stroke="var(--accent)"/><path d="M1.5 2.5L5 5.2l3.5-2.7" fill="none" stroke="var(--accent)"/></svg></i>info@virelahairstudio.com</div>
      <p class="footer-head" style="left:320px">Instagram</p>
      <div class="insta">
        <div role="img" aria-label="Instagram post: hair extension result" style="background:linear-gradient(135deg,#c89870,#6a4a3a)"></div>
        <div role="img" aria-label="Instagram post: hair extension result" style="background:linear-gradient(135deg,#3a2a2a,#b07850)"></div>
        <div role="img" aria-label="Instagram post: hair extension result" style="background:linear-gradient(135deg,#d8b080,#7a5030)"></div>
        <div role="img" aria-label="Instagram post: hair extension result" style="background:linear-gradient(135deg,#e0c090,#a07050)"></div>
        <div role="img" aria-label="Instagram post: hair extension result" style="background:linear-gradient(135deg,#5a3a30,#c09070)"></div>
        <div role="img" aria-label="Instagram post: hair extension result" style="background:linear-gradient(135deg,#d8a890,#4a3028)"></div>
      </div>
      <p class="footer-bar">Copyright © 2023 <b>Virela Hair Extensions</b>. All rights reserved.</p>
    </footer>
  </div>
</section>

<!-- ============ OPTION 2 : IVORY ============ -->
<section class="board board--dark">
  <h2 class="option-label">OPTION 2</h2>
  <div class="site site--ivory">
    <div class="hero">
      <div class="photo" role="img" aria-label="Woman in profile with long flowing chestnut brown hair" style="left:0;top:46px;width:457px;height:242px;background:radial-gradient(ellipse at 80% 40%,#c08868,#5a3020 45%,#2a1610 85%)"></div>
      <p class="eyebrow" style="left:25px;top:115px">Specialise in</p>
      <h1 class="hero-title">Finest Installation</h1>
      <p class="hero-sub">&amp; HAIR QUALITY</p>
      <p class="hero-text">I have been doing weave hair extensions for <b>16 years</b></p>
      <a class="btn" style="left:25px;top:202px;width:70px">Explore more</a>
      <div class="slider-dots" style="left:221px"><i></i><i></i><i></i></div>
    </div>

    <div class="topbar">
      <span class="dot" style="left:25px"></span><span class="dot" style="left:35px"></span><span class="dot" style="left:45px"></span>
      <span class="info" style="left:276px"><svg viewBox="0 0 10 10"><circle cx="5" cy="5" r="4.5" fill="none" stroke="#fff" stroke-width=".8"/><path d="M3.3 3c.3 1.8 1.6 3.3 3.4 3.8l.5-.8-1-.6-.5.4c-.6-.3-1.1-.8-1.4-1.4l.4-.5-.6-1z" fill="#fff"/></svg>+61 3 9555 0413</span>
      <span class="info" style="left:345px"><svg viewBox="0 0 10 10"><circle cx="5" cy="5" r="4.5" fill="none" stroke="#fff" stroke-width=".8"/><rect x="2.8" y="3.5" width="4.4" height="3" fill="none" stroke="#fff" stroke-width=".6"/><path d="M2.8 3.5L5 5.2l2.2-1.7" fill="none" stroke="#fff" stroke-width=".6"/></svg>info@virelahairstudio.com</span>
    </div>
    <header class="header">
      <div class="brand">Virela</div>
      <nav class="menu"><span class="is-active">Home</span><span>About us</span><span>Services</span><span>Gallery</span><span>News</span><span>Contact us</span></nav>
    </header>

    <section class="about">
      <div class="about-media">
        <div class="photo" role="img" aria-label="Woman with long wavy blonde hair in front of a flower wall" style="left:40px;top:28px;width:147px;height:178px;background:linear-gradient(160deg,#a83040,#e8d0b0 45%,#2a2a2a)"></div>
        <div class="badge"><strong>16</strong><span>Years of<br>Experience</span></div>
      </div>
      <div class="about-body">
        <p class="eyebrow" style="left:36px;top:48px">Welcome to</p>
        <h2 class="heading" style="left:36px;top:58px">Virela Hair Extensions</h2>
        <p class="copy" style="left:36px;top:86px;width:170px;color:#666">Sed ut perspiciatis unde omnis iste natus error sit voluptatem accusantium doloremque laudantium, totam rem aperiam, eaque ipsa quae ab illo inventore veritatis et quasi architecto beatae vitae dicta sunt explicabo. Nemo enim ipsam voluptatem quia voluptas sit aspernatur aut odit aut fugit, sed quia consequuntur magni dolores eos qui ratione voluptatem sequi nesciunt.</p>
        <a class="btn" style="left:36px;top:170px;width:62px">Read more</a>
      </div>
    </section>

    <section class="offer">
      <p class="eyebrow centered" style="top:35px">Victoria Australia</p>
      <h2 class="heading centered" style="top:45px">Hair Extensions Offer</h2>
      <div class="photo" role="img" aria-label="Back view of long straight platinum blonde flat hair extensions" style="left:25px;top:95px;width:110px;height:136px;background:linear-gradient(180deg,#5d6670,#d8d0c0 40%,#bdb3a0)"></div>
      <div class="offer-feature" role="img" aria-label="Back view of long blonde tiny hair extensions in a salon"><p class="cap">TinyHair Extension</p><p class="sub">Sed ut perspiciatis unde omnis iste natus error sit voluptatem</p></div>
      <div class="photo" role="img" aria-label="Back view of long blonde weave hair extensions" style="left:321px;top:95px;width:111px;height:136px;background:linear-gradient(180deg,#4a5560,#c7b99f 45%,#2a2a2a)"></div>
      <p class="offer-caption" style="left:25px">Flat Hair Extension</p>
      <p class="offer-caption" style="left:321px">Weave Hair Extension</p>
      <p class="pager" style="left:25px">⟵&nbsp;&nbsp;Prev</p>
      <p class="pager" style="right:25px">Next&nbsp;&nbsp;⟶</p>
    </section>

    <section class="services">
      <p class="eyebrow centered" style="top:35px">What we do</p>
      <h2 class="heading centered" style="top:45px;color:#fff">Our Services</h2>
      <div class="service" style="left:25px;top:75px"><div class="pic" role="img" aria-label="Stylist sectioning hair with clips" style="background:linear-gradient(135deg,#e0e0e0,#555)"></div><p class="tag">Victoria</p><p class="name">Weave hair Extensions</p><p class="desc">Duis aute irure dolor in reprehenderit in voluptate velit esse cillum... <em>Read More</em></p></div>
      <div class="service" style="left:163px;top:75px"><div class="pic" role="img" aria-label="Stylist straightening long blonde hair" style="background:linear-gradient(135deg,#8a6a40,#d8b070 50%,#e0c040)"></div><p class="tag">Australia</p><p class="name">Weave hair Extensions</p><p class="desc">Duis aute irure dolor in reprehenderit in voluptate velit esse cillum... <em>Read More</em></p></div>
      <div class="service" style="left:300px;top:75px"><div class="pic" role="img" aria-label="Stylist curling long brown hair" style="background:linear-gradient(135deg,#eee,#7a5a40 60%,#3a2a20)"></div><p class="tag">Professional</p><p class="name">Weave hair Extensions</p><p class="desc">Duis aute irure dolor in reprehenderit in voluptate velit esse cillum... <em>Read More</em></p></div>
      <div class="service" style="left:25px;top:228px"><div class="pic" role="img" aria-label="Hands attaching a blonde extension weft" style="background:linear-gradient(135deg,#f0e0c0,#d8a860)"></div><p class="tag">High-quality</p><p class="name">Weave hair Extensions</p><p class="desc">Duis aute irure dolor in reprehenderit in voluptate velit esse cillum... <em>Read More</em></p></div>
      <div class="service" style="left:163px;top:228px"><div class="pic" role="img" aria-label="Stylist parting dark hair to fit extensions" style="background:linear-gradient(135deg,#8a6a55,#4a3020)"></div><p class="tag">Natural-looking</p><p class="name">Weave hair Extensions</p><p class="desc">Duis aute irure dolor in reprehenderit in voluptate velit esse cillum... <em>Read More</em></p></div>
      <div class="service" style="left:300px;top:228px"><div class="pic" role="img" aria-label="Hair extension bundles with scissors and tools" style="background:linear-gradient(135deg,#2a2a2a,#9a7040 55%,#1a1a1a)"></div><p class="tag">Customizable</p><p class="name">Weave hair Extensions</p><p class="desc">Duis aute irure dolor in reprehenderit in voluptate velit esse cillum... <em>Read More</em></p></div>
      <a class="btn" style="left:188px;top:400px;width:80px">View all services</a>
    </section>

    <section class="specialists">
      <div class="photo" role="img" aria-label="Two women in camel blazers with long brunette hair" style="left:0;top:36px;width:160px;height:202px;background:linear-gradient(160deg,#f0ece8,#c49a78 55%,#4a3528)"></div>
      <p class="eyebrow" style="left:183px;top:35px">Certified</p>
      <h2 class="heading" style="left:183px;top:45px">Hair Extension Specialists</h2>
      <p class="copy" style="left:183px;top:72px;width:248px;color:#666">Sed ut perspiciatis unde omnis iste natus error sit voluptatem accusantium doloremque laudantium, totam rem aperiam eaque ipsa quae ab illo inventore veritatis et quasi architecto beatae vitae dicta sunt...</p>
      <a class="btn" style="left:183px;top:115px;width:62px">Read more</a>
      <div class="photo" role="img" aria-label="Before: back view of shoulder-length brown hair" style="left:288px;top:142px;width:81px;height:97px;background:linear-gradient(180deg,#3a7aa8,#5a3020 50%,#2a1a10)"><p class="before-after" style="bottom:8px">Before</p></div>
      <div class="photo" role="img" aria-label="After: back view of long wavy brown hair extensions" style="left:377px;top:170px;width:80px;height:100px;background:linear-gradient(160deg,#5a9ac0,#8a5028 50%,#3a2010)"><p class="before-after" style="bottom:8px">After</p></div>
    </section>

    <section class="testimonials">
      <p class="eyebrow centered" style="top:35px">Testimonials</p>
      <h2 class="heading centered" style="top:45px;color:#fff">Our Satisfied Customer</h2>
      <span class="arrow-nav" style="left:11px">‹</span><span class="arrow-nav" style="right:11px">›</span>
      <div class="quote-card" style="left:25px"><p class="mark">“</p><p>“Sed ut perspiciatis unde omnis iste natus error sit voluptatem accusantium doloremque laudantium, totam rem aperiam, eaque ipsa quae ab illo inventore veritatis et quasi architecto beatae enim ipsam voluptatem quia voluptas sit”</p></div>
      <div class="quote-card" style="left:163px"><p class="mark">“</p><p>“Sed ut perspiciatis unde omnis iste natus error sit voluptatem accusantium doloremque laudantium, totam rem aperiam, eaque ipsa quae ab illo inventore veritatis et quasi architecto beatae enim ipsam voluptatem quia voluptas sit”</p></div>
      <div class="quote-card" style="left:300px"><p class="mark">“</p><p>“Sed ut perspiciatis unde omnis iste natus error sit voluptatem accusantium doloremque laudantium, totam rem aperiam, eaque ipsa quae ab illo inventore veritatis et quasi architecto beatae enim ipsam voluptatem quia voluptas sit”</p></div>
      <div class="reviewer" style="left:25px"><div class="avatar" role="img" aria-label="Customer portrait"></div><div><b>Mara Ellison</b><span>Happy Customer</span></div></div>
      <div class="reviewer" style="left:163px"><div class="avatar" role="img" aria-label="Customer portrait"></div><div><b>Tessa Dunmore</b><span>Happy Customer</span></div></div>
      <div class="reviewer" style="left:300px"><div class="avatar" role="img" aria-label="Customer portrait"></div><div><b>Clara Whitby</b><span>Happy Customer</span></div></div>
    </section>

    <section class="keywords">
      <div class="cell photo" role="img" aria-label="Blonde woman with long wavy hair" style="left:0;top:0;background:linear-gradient(135deg,#e8d8c0,#b09070)"></div>
      <div class="cell cell--text" style="left:152px;top:0"><small>Affordable</small><strong>Weave</strong><span>Hair Extensions</span></div>
      <div class="cell photo" role="img" aria-label="Black and white portrait of a woman with long dark hair in a satin dress" style="left:304px;top:0;width:153px;height:194px;background:linear-gradient(160deg,#bbb,#555 60%,#222)"></div>
      <div class="cell cell--text" style="left:0;top:97px"><small>Victoria</small><strong>Weave Hair</strong><span>Extensions Service</span></div>
      <div class="cell photo" role="img" aria-label="Stylist blow-drying a client's long brown hair" style="left:152px;top:97px;background:linear-gradient(135deg,#3a5a70,#8a6a50)"></div>
      <div class="cell photo" role="img" aria-label="Woman with long black hair beside pink blossoms" style="left:0;top:194px;background:linear-gradient(135deg,#e8c8c8,#2a2a2a 60%,#d8b0b0)"></div>
      <div class="cell cell--text" style="left:152px;top:194px"><small>Top-Rated</small><strong>Weave Hair</strong><span>Extensions Salon</span></div>
      <div class="cell cell--text cell--mocha" style="left:304px;top:194px;width:153px"><small>Victoria's</small><strong>Premier</strong><span>Wave Hair Extensions</span></div>
    </section>

    <section class="newsletter" role="img" aria-label="Dark background portrait of a woman with flowing hair">
      <p class="eyebrow centered" style="top:47px">Subscribe</p>
      <h2 class="heading centered" style="top:57px">Our Newsletter</h2>
      <p class="copy centered" style="top:78px;color:#bbb">Duis aute irure dolor in reprehenderit in voluptate velit esse cillum dolore</p>
      <div class="signup"><svg viewBox="0 0 10 10"><rect x="1" y="2" width="8" height="6" fill="none" stroke="#999"/><path d="M1 2l4 3 4-3" fill="none" stroke="#999"/></svg>Enter Your Email<a class="btn">Subscribe</a></div>
    </section>

    <footer class="footer">
      <div class="brand">Virela</div>
      <p class="footer-copy">Duis aute irure dolor in reprehenderit in voluptate velit esse cillum dolore eu fugiat nulla pariatur...</p>
      <span class="social-square" style="left:25px"></span><span class="social-square" style="left:40px"></span><span class="social-square" style="left:55px"></span>
      <p class="footer-head" style="left:140px">Quick links</p>
      <p class="footer-links" style="left:140px">Home<br>About Us<br>Services<br>Gallery<br>News<br>Contact Us</p>
      <p class="footer-head" style="left:215px">Contacts</p>
      <div class="contact-row" style="left:215px;top:44px;width:90px"><i><svg viewBox="0 0 10 10"><path d="M5 1a3 3 0 0 1 3 3c0 2.3-3 5-3 5S2 6.3 2 4a3 3 0 0 1 3-3z" fill="var(--accent)"/></svg></i>12 Lorem ipsum dolor sit amet<br>Ballarat VIC 3350</div>
      <div class="contact-row" style="left:215px;top:69px"><i><svg viewBox="0 0 10 10"><path d="M2 1.5c.4 3.4 3 6 6.5 6.6l.8-1.6-2-1.2-1 .8C5 5.5 4.3 4.8 3.9 3.8l.8-1-1.2-2z" fill="var(--accent)"/></svg></i>+61 3 9555 0413</div>
      <div class="contact-row" style="left:215px;top:91px"><i><svg viewBox="0 0 10 10"><rect x="1.5" y="2.5" width="7" height="5" fill="none" stroke="var(--accent)"/><path d="M1.5 2.5L5 5.2l3.5-2.7" fill="none" stroke="var(--accent)"/></svg></i>info@virelahairstudio.com</div>
      <p class="footer-head" style="left:320px">Instagram</p>
      <div class="insta">
        <div role="img" aria-label="Instagram post: hair extension result" style="background:linear-gradient(135deg,#c89870,#6a4a3a)"></div>
        <div role="img" aria-label="Instagram post: hair extension result" style="background:linear-gradient(135deg,#3a2a2a,#b07850)"></div>
        <div role="img" aria-label="Instagram post: hair extension result" style="background:linear-gradient(135deg,#d8b080,#7a5030)"></div>
        <div role="img" aria-label="Instagram post: hair extension result" style="background:linear-gradient(135deg,#e0c090,#a07050)"></div>
        <div role="img" aria-label="Instagram post: hair extension result" style="background:linear-gradient(135deg,#5a3a30,#c09070)"></div>
        <div role="img" aria-label="Instagram post: hair extension result" style="background:linear-gradient(135deg,#d8a890,#4a3028)"></div>
      </div>
      <p class="footer-bar">Copyright © 2023 <b>Virela Hair Extensions</b>. All rights reserved.</p>
    </footer>
  </div>
</section>

</body>
</html>
```